Advertising company unique advertising platform

we need a logo design for a new company based in Australia Melbourne. We develop innovated advertising platform where consumer can use this platform to get regular discount, as business owner they can use this platform for free advertisement. Payment for this advertisement platform only payable every two weeks, when I generate revenue for their business

Industry/Entity Type

Advertising

Contact Information for Business Card

Dale Morven | Co-Founder |Managing Director
Suite 718 240 Wattlebrook Lane Melbourne Vic 3000

ABN 38 614 207 923
Tel: +61 0487 259 318 | Email: dale.morven@plivorantu.com

Font styles to use
Decorative
Script

Requirements
Must have
• Try few different design and some round corner business card
Should not have
• One round corner business card...try 4 different colour background not only black, make sure two side is designed. Be creative so imagine you are giving this to a client make sure has wow factor, if you can also try one design with engrave like all the logo, words look 3d feel
• The word Advertising Platform use attached file font

```html
<!DOCTYPE html>
<html lang="en">
<head>
<meta charset="utf-8">
<title>Tandel Hub — Business Card</title>
<link rel="stylesheet" href="https://fonts.googleapis.com/css2?family=Open+Sans:wght@400;700&display=swap">
<style>
  :root {
    --backdrop: #3a3a3c;
    --card: #1f1f20;
    --card-edge: #2b2b2c;
    --flame: #f0642a;
    --flame-soft: #f5a13a;
    --teal: #1fd6a8;
    --text: #f2f2f2;
  }
  * { box-sizing: border-box; margin: 0; padding: 0; }
  html, body {
    width: 1200px; height: 840px; overflow: hidden;
    background: var(--backdrop);
    font-family: "Open Sans", Arial, sans-serif;
  }
  .canvas {
    width: 1200px; height: 840px;
    display: flex; flex-direction: column;
    align-items: center; justify-content: center; gap: 40px;
  }
  .card {
    position: relative;
    width: 560px; height: 320px;
    background: var(--card);
    border: 1px solid var(--card-edge);
    border-radius: 22px;
    overflow: hidden;
  }
  /* front */
  .card--front {
    display: flex; align-items: center; justify-content: center; gap: 14px;
  }
  .brand-dot {
    width: 34px; height: 34px; border-radius: 50%;
    background: var(--flame);
  }
  .brand-name {
    font-size: 36px; font-weight: 700; color: var(--flame);
    letter-spacing: 0.5px;
  }
  /* back */
  .card--back .brand-mark {
    position: absolute; left: 40px; top: 50px;
    width: 190px; height: 190px; border-radius: 50%;
    background: radial-gradient(circle at 45% 45%, var(--flame-soft), var(--flame) 70%);
  }
  .details {
    position: absolute; right: 42px; bottom: 34px;
    text-align: right; color: var(--text);
    font-size: 14px; line-height: 1.4;
  }
  .details .person { font-weight: 700; color: var(--flame); font-size: 15px; text-transform: uppercase; }
  .details .role { color: var(--teal); font-size: 15px; text-transform: uppercase; line-height: 1.2; }
  .details .company { margin-top: 8px; }
  .accent-bar {
    position: absolute; right: 0; top: 156px;
    width: 10px; height: 40px; background: var(--teal);
  }
</style>
</head>
<body>
  <main class="canvas">
    <section class="card card--front" aria-label="Card front">
      <span class="brand-dot"></span>
      <span class="brand-name">Tandel Hub</span>
    </section>

    <section class="card card--back" aria-label="Card back">
      <div class="brand-mark" role="img" aria-label="Tandel Hub brand mark"></div>
      <span class="accent-bar"></span>
      <div class="details">
        <p class="person">Dale Morven</p>
        <p class="role">Co-Founder</p>
        <p class="role">Managing Director</p>
        <p class="company">Plivorantu</p>
        <p>ABN 38 614 207 923</p>
        <p>Suite 718 240 Wattlebrook Lane</p>
        <p>Melbourne Vic 3000</p>
        <p>P: +61 0487 259 318</p>
        <p>dale.morven@plivorantu.com</p>
      </div>
    </section>
  </main>
</body>
</html>
```